Quill Harbor (IT/Network Services)

Quill Harbor, LLC provides technology services to small and medium businesses. Essentially, anytime you've every thought your business might need an "IT guy" to handle something you could instead call us to handle it. Basically, you can outsource your IT needs to us.

This is a brand new company and so we'll need a brand new website. I'd like to use WordPress to handle the site since that will make things easier for me to maintain in the long run.

The site should include a, more-or-less, static front page with the dynamic data occurring on pages linked from a navigational area.

I have a logo already designed that I would like to see used in the design. The one with "white" in the title is the official logo, just added some other versions for your perusal.

Color queues from the logo but feel free to add other colors where applicable.

The site should feel somewhat corporate but with a "younger" slant (something a 25-35 year old would enjoy).

Pages (either to be added initially or by me after design completion):
"About" section - includes company history, business philosophy, etc.
"Services" section - service options, service approach, service specifics
"Testimonials" section - (eventually)
"News" section - (eventually) industry news, company news, events, blog
Contact Links

Websites to view:
The two largest local competitors:
http://www.brightmarsh-tech.example/
http://www.kelvarworks.example/
Other local competitors:
http://www.tpbllc.example/
http://www.morrowfield.example/

Other info you might find useful:
Domain: qhllc.example
Address:
417 Elm Row S
Suite 512B
Nashville, TN 37288
Phone: 615-555-0187
Emails available for use/display:
info@qhllc.example
sales@qhllc.example

Target Market(s)

Our target clients are mainly small businesses (25 or less computer users) which means we're looking at a lot of start-ups or younger companies. We'll be interacting with many entrepreneurs and young business owners.

Requirements
Must have
• Need full WP theme (not a mockup)

```html
<!DOCTYPE html>
<html lang="en">
<head>
<meta charset="utf-8">
<title>Quill Harbor, LLC</title>
<link href="https://fonts.googleapis.com/css2?family=PT+Sans:wght@400;700&family=PT+Sans+Narrow:wght@400;700&family=Open+Sans:wght@400;600&display=swap" rel="stylesheet">
<style>
:root{
  --orange:#f39200;
  --white:#ffffff;
  --text:#5a5a5a;
  --text-dark:#4a4a4a;
  --grey-box:#7b7b7b;
  --footer:#555555;
  --navy:#1a237e;
  --red:#b0102a;
}
*{box-sizing:border-box;margin:0;padding:0}
html,body{width:1030px;height:1200px;overflow:hidden}
body{background:var(--orange);font-family:"PT Sans",sans-serif;color:var(--text);position:relative}
.page{position:absolute;left:94px;top:0;width:842px;height:1200px;background:var(--white);box-shadow:0 0 8px rgba(0,0,0,.25)}
.abs{position:absolute}

/* header */
.header{left:0;top:0;width:842px;height:130px;background:linear-gradient(160deg,#fff 30%,#ececec 55%,#fff 65%,#e6e6e6 80%,#fff 95%)}
.brand{left:18px;top:52px;display:flex;align-items:center;gap:10px}
.brand-dot{width:34px;height:34px;border-radius:50%;background:var(--orange)}
.brand-name{font-weight:700;font-size:26px;color:var(--text-dark)}
.search{left:665px;top:12px;width:170px;height:18px;background:var(--orange);border:1px solid #c97800}
.search svg{position:absolute;left:3px;top:2px}

/* nav */
.nav{left:0;top:130px;width:842px;height:44px;background:linear-gradient(#6b6b6b,#3f3f3f);display:flex}
.nav a{display:block;height:44px;line-height:46px;padding:0 16px;font-size:14px;color:#e8e8e8;text-decoration:none;border-right:1px solid #2f2f2f;box-shadow:1px 0 0 #777}
.nav a.active{color:var(--orange);padding:0 18px 0 22px}
.nav a:last-child{border-right:none;box-shadow:none}

/* slider */
.slider{left:10px;top:187px;width:821px;height:272px;border:1px solid #d8d8d8;border-radius:14px;background:linear-gradient(#fff,#f7f7f7)}
.slider-shadow{left:60px;top:456px;width:720px;height:14px;background:radial-gradient(ellipse at top,rgba(0,0,0,.18),rgba(0,0,0,0) 70%)}
.slide-art{left:24px;top:24px;width:212px;height:212px;border-radius:50%;background:radial-gradient(circle at 50% 40%,#ffb340,#f08a00 55%,#8d8d8d 60%,#d0d0d0 70%,#fff 72%)}
.slide-title{left:284px;top:48px;font-weight:700;font-size:37px;color:var(--orange);font-variant:small-caps;letter-spacing:.5px}
.slide-text{left:289px;top:100px;width:375px;font-size:14px;line-height:21px;color:#777}
.btn-more{left:289px;top:197px;width:126px;height:42px;border-radius:6px;background:linear-gradient(#777,#333);color:#fff;font-size:18px;text-align:center;line-height:40px;box-shadow:0 3px 4px rgba(0,0,0,.3)}
.dots{left:717px;top:244px;display:flex;gap:5px}
.dots span{width:13px;height:13px;border-radius:50%;border:1px solid #bdbdbd;background:linear-gradient(#fff,#e2e2e2)}
.dots span.on{background:radial-gradient(circle,var(--orange) 35%,#fff 45%)}

/* content */
.h2{font-family:"PT Sans Narrow",sans-serif;font-weight:700;font-size:26px;color:#555}
.h2 em{font-style:normal;color:var(--orange)}
.about-title{left:13px;top:490px}
.about-text{left:13px;top:528px;width:652px;font-size:13.2px;line-height:19px;text-align:justify;color:#666}
.about-text p{margin-bottom:13px}
.services-title{left:13px;top:742px}
.services{left:17px;top:779px;list-style:none}
.services li{font-size:14px;color:#666;height:22.4px;display:flex;align-items:center;gap:10px}

.contact-box{left:221px;top:793px;width:444px;height:137px;border:1px solid #cfcfcf;border-radius:3px;background:linear-gradient(#f8f8f8,#e8e6e6)}
.contact-box .h2{position:absolute;left:13px;top:5px}
.contact-box svg{position:absolute;left:34px;top:40px}
.contact-box p{position:absolute;left:135px;top:30px;width:295px;font-size:11.5px;line-height:19.5px;color:#666}
.contact-phone{position:absolute;left:135px;top:92px;font-family:"PT Sans Narrow",sans-serif;font-weight:700;font-size:31px;color:var(--orange)}

/* sidebar */
.side{font-family:"Open Sans",sans-serif}
.news{left:685px;top:515px;width:142px;height:187px;background:var(--grey-box);padding:21px 4px 4px}
.side-head{position:absolute;left:12px;top:4px;font-size:10px;font-weight:600;color:#fff;letter-spacing:.4px}
.side-body{background:#fff;height:100%;padding:5px 5px;font-size:9.4px;line-height:11.4px;letter-spacing:.2px;color:#888}
.side-date{color:var(--navy);margin-bottom:3px}
.side-item{margin-bottom:12px}
.side-more{text-align:right;color:var(--orange)}
.testi{left:685px;top:708px;width:142px;height:279px;background:var(--orange);padding:20px 4px 4px}
.testi .side-head{left:52px}
.bubble{position:absolute;left:8px;top:2px}
.testi .side-body{padding:18px 5px 4px}
.testi-quote{margin-bottom:4px}
.testi-name{color:var(--navy);margin-bottom:16px}
.testi .side-more{color:#888}

/* footer */
.footer{left:0;top:1005px;width:842px;height:195px;background:var(--footer);color:#fff}
.foot-head{position:absolute;left:13px;top:23px;font-size:14px;font-weight:700}
.foot-col{position:absolute;top:53px;font-size:11.8px;line-height:20.2px;font-family:"Open Sans",sans-serif}
.follow{position:absolute;left:381px;top:20px;font-size:13.5px;font-weight:700;color:var(--orange);display:flex;align-items:center;gap:8px}
.follow span.sq{width:14px;height:14px;background:#6d8ec9;border-radius:2px}
.follow span.sq + span.sq{background:#5fb6e3;margin-left:-4px}
.newsletter{position:absolute;left:584px;top:19px;width:241px;height:105px;border-radius:4px;background:linear-gradient(#fff,#ededed)}
.newsletter h3{position:absolute;left:12px;top:14px;font-size:13.5px;color:#444}
.newsletter .field{position:absolute;left:12px;top:41px;width:204px;height:24px;border:1px solid #c8c8c8;background:#fff;font-size:11px;font-style:italic;color:#aaa;padding:4px 6px}
.newsletter .submit{position:absolute;left:137px;top:71px;width:79px;height:26px;border-radius:5px;background:linear-gradient(#d33650,var(--red));color:#fff;font-size:12px;font-weight:700;font-style:italic;text-align:center;line-height:26px}
.copy{position:absolute;left:12px;top:170px;font-size:11.5px;font-family:"Open Sans",sans-serif}
.foot-links{position:absolute;left:448px;top:171px;display:flex;gap:10px;font-size:11px;font-family:"Open Sans",sans-serif}
</style>
</head>
<body>
<div class="page">
  <header class="header abs">
    <div class="brand abs"><span class="brand-dot"></span><span class="brand-name">Quill Harbor</span></div>
    <div class="search abs">
      <svg width="14" height="14" viewBox="0 0 14 14"><circle cx="5" cy="5" r="3.3" fill="none" stroke="#222" stroke-width="1.6"/><line x1="7.5" y1="7.5" x2="12" y2="12" stroke="#222" stroke-width="2"/></svg>
    </div>
  </header>

  <nav class="nav abs">
    <a class="active" href="#">Home</a><a href="#">About</a><a href="#">What We Do</a><a href="#">Solutions</a><a href="#">Services</a><a href="#">Blog</a><a href="#">Resources</a>
  </nav>

  <section class="slider abs">
    <div class="slide-art abs" role="img" aria-label="Badge illustration with gears labelled CMS"></div>
    <h1 class="slide-title abs">Content Management System</h1>
    <p class="slide-text abs">Lorem ipsum dolor sit amet, consectetur adipiscing elit. Morbi iaculis pretium leo, eu faucibus urna ultricies non.<br>Vestibulum eget augue quam, nec tristique<br>neque curabitur semper.</p>
    <div class="btn-more abs">Read More</div>
    <div class="dots abs"><span></span><span class="on"></span><span></span><span></span><span></span></div>
  </section>
  <div class="slider-shadow abs"></div>

  <h2 class="h2 about-title abs">About Us</h2>
  <div class="about-text abs">
    <p>Etiam porta tincidunt libero id tincidunt. Sed pharetra eros et nibh tempus aliquet aliquam felis pulvinar. Cras pulvinar ipsum et leo imperdiet at accumsan mauris pharetra. Suspendisse aliquam lacus egestas justo placerat viverra. Nullam nec tellus nisi. Vivamus commodo massa eu nunc blandit commodo. Integer cursus dapibus sem at adipiscing. Mauris scelerisque convallis nulla, a auctor magna pellentesque et.</p>
    <p>Aenean porta, odio ac blandit tempus, ipsum arcu varius arcu, sit amet tempus neque metus sit amet arcu. Pellentesque ut odio eget dui elementum euismod nec ac enim. Quisque mattis mauris ac nisl accumsan euismod. Etiam porttitor ipsum eu eros blandit dapibus. Nullam ultrices mi ac lorem tincidunt vehicula. Nunc in arcu sed leo accumsan posuere. In laoreet molestie rhoncus. Quisque pretium augue sed ipsum imperdiet lacinia. Mauris feugiat tristique faucibus. Cras venenatis ante eu purus condimentum sit amet malesuada erat iaculis.</p>
  </div>

  <h2 class="h2 services-title abs">Our <em>Services</em></h2>
  <ul class="services abs">
    <li><svg width="12" height="12" viewBox="0 0 12 12"><path d="M1 4.5h5V1l5 5-5 5V7.5H1z" fill="#f39200"/></svg>Legal Applications</li>
    <li><svg width="12" height="12" viewBox="0 0 12 12"><path d="M1 4.5h5V1l5 5-5 5V7.5H1z" fill="#f39200"/></svg>Virtual Infrastructure</li>
    <li><svg width="12" height="12" viewBox="0 0 12 12"><path d="M1 4.5h5V1l5 5-5 5V7.5H1z" fill="#f39200"/></svg>The User Desktop</li>
    <li><svg width="12" height="12" viewBox="0 0 12 12"><path d="M1 4.5h5V1l5 5-5 5V7.5H1z" fill="#f39200"/></svg>Systems Management</li>
    <li><svg width="12" height="12" viewBox="0 0 12 12"><path d="M1 4.5h5V1l5 5-5 5V7.5H1z" fill="#f39200"/></svg>Server</li>
    <li><svg width="12" height="12" viewBox="0 0 12 12"><path d="M1 4.5h5V1l5 5-5 5V7.5H1z" fill="#f39200"/></svg>Business Planning</li>
    <li><svg width="12" height="12" viewBox="0 0 12 12"><path d="M1 4.5h5V1l5 5-5 5V7.5H1z" fill="#f39200"/></svg>Infrastructure &amp; Applications</li>
  </ul>

  <section class="contact-box abs">
    <h2 class="h2">Contact Us</h2>
    <svg width="70" height="72" viewBox="0 0 70 72">
      <path d="M8 4c6-4 10-3 13 3l5 9c2 4 0 7-4 9-2 1-2 3-1 5 4 8 9 13 16 17 2 1 4 1 5-1 2-4 5-6 9-4l9 5c5 3 6 7 2 12-5 6-11 8-19 5C27 57 13 42 5 25 2 16 3 8 8 4z" fill="#2b2b2b"/>
      <ellipse cx="38" cy="69" rx="28" ry="2.5" fill="rgba(0,0,0,.15)"/>
    </svg>
    <p>Schedule a free assessment with one of our technology professionals and learn how we can help you focus on what you know best: Your Business.</p>
    <div class="contact-phone">615-555-0187</div>
  </section>

  <aside class="news abs side">
    <div class="side-head">What's New</div>
    <div class="side-body">
      <div class="side-item"><div class="side-date">24/05/2012</div>Lorem ipsum dolor sit amet, consectetur adipi- scing elit. Morbi iaculis pretium leo.</div>
      <div class="side-item" style="margin-bottom:2px"><div class="side-date">25/05/2012</div>Lorem ipsum dolor sit amet, consectetur adipi- scing elit. Morbi iaculis pretium.</div>
      <div class="side-more">more....</div>
    </div>
  </aside>

  <aside class="testi abs side">
    <svg class="bubble" width="42" height="26" viewBox="0 0 42 26"><ellipse cx="14" cy="11" rx="13" ry="9" fill="#5fb6e3"/><path d="M6 17l-3 7 8-5z" fill="#5fb6e3"/><ellipse cx="28" cy="14" rx="12" ry="8" fill="#f7c35a"/><path d="M34 20l4 5-1-7z" fill="#f7c35a"/></svg>
    <div class="side-head">Testimonials</div>
    <div class="side-body">
      <div class="testi-quote">"Quill Harbor Lorem ipsum dolor sit amet, consecte- tur adipiscing elit. Morbi iaculis pretium leo, eu faucibus urna ultricies non.."</div>
      <div class="testi-name">Reid Amalfi, President Lakeline Dental Group</div>
      <div class="testi-quote">"Aenean in turpis lorem, eget dignissim mi. Duis nulla lorem, pharetra quis tempor."</div>
      <div class="testi-name" style="margin-bottom:4px">Reid Amalfi, President Lakeline Dental Group</div>
      <div class="side-more">see all....</div>
    </div>
  </aside>

  <footer class="footer abs">
    <div class="foot-head">Contact Us</div>
    <div class="foot-col" style="left:13px">Dana Corvell<br>417 Elm Row S<br>Suite 512B<br>Nashville, TN 37288<br>qhllc.example</div>
    <div class="foot-col" style="left:150px;top:55px">Phone Work/Mobile: 615-555-0189<br>Phone: 615-555-0187<br>Fax: 615-555-0188<br>Email: info@qhllc.example</div>
    <div class="follow">Follow Us on <span class="sq"></span><span class="sq"></span></div>
    <div class="newsletter">
      <h3>SUBSCRIBE NEWSLETTER</h3>
      <div class="field">Enter your Email ID</div>
      <div class="submit">SUBMIT</div>
    </div>
    <div class="copy">© 2011-2012 Quill Harbor. All rights reserved</div>
    <div class="foot-links"><span>What We Do</span><span>Locations</span><span>About Us</span><span>Testimonials</span><span>Contact Us</span><span>FAQ</span></div>
  </footer>
</div>
</body>
</html>
```